Catalogue Cover, spine and Divider pages

Design the cover, spine and divider pages for our first hard copy catalogue in line with the existing CD Cover design recently completed.

Cover size is 313mm h x 292mm w
Spine is 313mm h x 93mm w

Requirements
Must have
• Company Logo to front cover dividers and spine, design in line with recent CD Cover design, Web Address to front cover, Company name in full to front cover, 1300 toll free number to front cover.
Sample attached files are only a guide for the use of each section we would like a fresh approach in line with the recent CD cover design.

```html
<!DOCTYPE html>
<html lang="en">
<head>
<meta charset="utf-8">
<title>Catalogue Divider Pages</title>
<link rel="stylesheet" href="https://fonts.googleapis.com/css2?family=Open+Sans:wght@600;700;800&display=swap">
<style>
  :root{
    --backdrop:#1d1d1d;
    --navy:#24398a;
    --navy-deep:#1b2d6e;
    --orange:#e2621f;
    --page-white:#ffffff;
    --page-grey:#e9e9ea;
    --page-grey-dark:#d6d6d8;
    --tab-grey:#e4e4e6;
    --caption-text:#ffffff;
  }
  *{box-sizing:border-box;margin:0;padding:0}
  html,body{width:1200px;height:1000px;overflow:hidden}
  body{background:var(--backdrop);font-family:"Open Sans",Arial,sans-serif;position:relative}

  .divider-page{position:absolute;top:100px;width:490px;height:800px}
  .divider-page .sheet{position:absolute;inset:0;border-radius:2px}
  .divider-meridian{left:50px}
  .divider-meridian .sheet{background:linear-gradient(160deg,var(--page-grey) 0%,#f4f4f5 45%,var(--page-grey-dark) 100%)}
  .divider-terrace{left:610px}
  .divider-terrace .sheet{background:var(--page-white)}

  .tab{position:absolute;left:100%;width:34px;height:100px;border-radius:0 10px 10px 0;
       display:flex;align-items:center;justify-content:center}
  .tab span{writing-mode:vertical-rl;font-size:7.5px;font-weight:800;color:var(--navy);
            letter-spacing:.3px;text-align:center;line-height:1.15}
  .tab.inactive{background:var(--tab-grey)}
  .tab.active{background:var(--page-white)}
  .divider-meridian .tab{background:var(--page-grey)}

  .section-title{position:absolute;left:32px;top:34px}
  .section-title .name{font-size:40px;font-weight:800;color:var(--navy);line-height:1;letter-spacing:1px}
  .section-title .sub{font-size:17px;font-weight:700;color:var(--navy);margin-top:2px;letter-spacing:.3px}

  .photo-card{position:absolute}
  .photo-card .photo{position:absolute;left:0;top:0;right:0;bottom:26px;border-radius:4px 4px 0 0}
  .photo-card .photo.split{display:flex;gap:10px;background:none}
  .photo-card .photo.split div{flex:1;border-radius:4px 4px 0 0}
  .caption{position:absolute;left:0;right:0;bottom:0;height:26px;background:var(--navy);
           border-radius:0 0 6px 6px;display:flex;align-items:center;padding-left:56px;
           color:var(--caption-text);font-size:10.5px;font-weight:700}
  .code{position:absolute;left:0;bottom:-8px;width:46px;height:34px;background:var(--navy-deep);
        border-radius:0 0 0 6px;color:var(--orange);font-weight:800;font-size:15px;
        display:flex;align-items:center;justify-content:center}

  .img-office{background:linear-gradient(180deg,#9fc1e0 0%,#8a94a0 55%,#6d6b66 100%)}
  .img-tower{background:linear-gradient(180deg,#a9cdea 0%,#dfe8ee 55%,#b8c3c9 100%)}
  .img-interior{background:linear-gradient(180deg,#e6e1d6 0%,#c9c1b0 60%,#9c8f78 100%)}
  .img-dining{background:linear-gradient(180deg,#cfc4b4 0%,#8b7e6e 60%,#4e4a45 100%)}
  .img-patio{background:linear-gradient(180deg,#c7cdd2 0%,#7c7468 55%,#3e3a35 100%)}
  .img-storefront{background:linear-gradient(180deg,#a7c5de 0%,#8f9aa3 55%,#7a7670 100%)}
  .img-estate{background:linear-gradient(180deg,#86b4e0 0%,#d9d2c6 50%,#7ea24f 100%)}
  .img-cafe{background:linear-gradient(180deg,#5c7894 0%,#3f6c8a 50%,#2f3b3a 100%)}
  .img-louvre{background:linear-gradient(180deg,#d9d9d6 0%,#bdbcb6 100%)}
</style>
</head>
<body>

<section class="divider-page divider-meridian" aria-label="Meridian Architectural Systems divider">
  <div class="sheet"></div>
  <div class="tab" style="top:20px"><span>MERIDIAN SYSTEMS</span></div>
  <header class="section-title">
    <div class="name">MERIDIAN</div>
    <div class="sub">ARCHITECTURAL SYSTEMS</div>
  </header>
  <figure class="photo-card" style="left:30px;top:130px;width:300px;height:150px">
    <div class="photo img-office" role="img" aria-label="Commercial building with glazed shopfront"></div>
    <figcaption class="caption">101.6mm Centre Glazed</figcaption><span class="code">C1</span>
  </figure>
  <figure class="photo-card" style="left:30px;top:300px;width:300px;height:150px">
    <div class="photo img-estate" role="img" aria-label="Industrial units with front glazed entries"></div>
    <figcaption class="caption">150 Front Glazed</figcaption><span class="code">C4</span>
  </figure>
  <figure class="photo-card" style="left:30px;top:470px;width:300px;height:150px">
    <div class="photo img-cafe" role="img" aria-label="Cafe interior behind double glazed frontage"></div>
    <figcaption class="caption">150mm Double Front Glazed</figcaption><span class="code">C7</span>
  </figure>
  <figure class="photo-card" style="left:30px;top:640px;width:300px;height:130px">
    <div class="photo img-louvre" role="img" aria-label="Fixed aluminium louvre panel"></div>
    <figcaption class="caption">Fixed Louvre</figcaption><span class="code">C10</span>
  </figure>
</section>

<section class="divider-page divider-terrace" aria-label="Terrace Bi-Fold Systems divider">
  <div class="sheet"></div>
  <div class="tab inactive" style="top:20px"><span>MERIDIAN SYSTEMS</span></div>
  <div class="tab inactive" style="top:125px"><span>SLIDING SYSTEMS</span></div>
  <div class="tab inactive" style="top:230px"><span>LOUVRE SYSTEMS</span></div>
  <div class="tab active" style="top:335px"><span>TERRACE SYSTEMS</span></div>
  <header class="section-title">
    <div class="name">Terrace</div>
    <div class="sub">BI-FOLD SYSTEMS</div>
  </header>
  <figure class="photo-card" style="left:30px;top:130px;width:430px;height:210px">
    <div class="photo split">
      <div class="img-office" role="img" aria-label="Modern office building with bi-fold glazing"></div>
      <div class="img-tower" role="img" aria-label="Residential tower with glazed balconies"></div>
    </div>
    <figcaption class="caption">Terrace Bi-Fold Door and Window</figcaption><span class="code">A1</span>
  </figure>
  <figure class="photo-card" style="left:30px;top:370px;width:250px;height:200px">
    <div class="photo img-interior" role="img" aria-label="Open centre mount bi-fold door in bright room"></div>
    <figcaption class="caption">Terrace Centre Mount Bi-Fold Door</figcaption><span class="code">A2</span>
  </figure>
  <figure class="photo-card" style="left:30px;top:600px;width:430px;height:170px">
    <div class="photo split">
      <div class="img-dining" role="img" aria-label="Dining area opening through bi-fold doors"></div>
      <div class="img-patio" role="img" aria-label="Outdoor patio with dining set beyond bi-fold doors"></div>
    </div>
    <figcaption class="caption">Terrace Bottom Rolling Bi-Fold Door</figcaption><span class="code">A3</span>
  </figure>
</section>

</body>
</html>
```